Elegant Business Card with Logo and Picture

Please create a business card that has the Logo colors add Gold and turquoise / use the attached logo - I would like a beautiful Business Card - Please make sure it's printed on both sides / Picture can go on one side Logo other
www.velmoragrove.com
614-372-0583
Lina Suzette Brolin
linasb@quorvamail.com
Life Coach
Thessing Certified Teacher / Life Coach / Interior Designer
Transformational Retreats

Target Market(s)

Women Men General

Industry/Entity Type

Life Coaching

Contact Information for Business Card

www.velmoragrove.com
614-372-0583
Lina Suzette Brolin
Life Coach
Thessing Certified Teacher / Yoga Teacher / Interior Designer

Font styles to use
Serif
Decorative

Colors
33a6d6
e34197
ffc214

Requirements
Must have
• Quality Paper and touch /
Nice to have
• Beautiful Touch and feel
Should not have
• needs to be elegant

```html
<!DOCTYPE html>
<html lang="en">
<head>
<meta charset="utf-8">
<title>Velmora Grove Coaching – Business Card</title>
<link href="https://fonts.googleapis.com/css2?family=Zilla+Slab:wght@300;400&family=Allura&display=swap" rel="stylesheet">
<style>
  :root{
    --bg:#2b2e33;
    --paper:#ffffff;
    --turquoise:#2fb5b8;
    --gold:#c9a227;
    --gold-deep:#b8891f;
    --gold-light:#f3e08a;
    --halo:#f4e27c;
    --ink:#5b5b5b;
    --ink-dark:#2a2418;
  }
  *{box-sizing:border-box;margin:0;padding:0}
  html,body{width:1200px;height:900px;overflow:hidden;background:var(--bg)}
  body{position:relative;font-family:"Zilla Slab",Georgia,serif}

  .card{position:absolute;left:250px;width:700px;height:400px;overflow:hidden;border-radius:4px;box-shadow:0 10px 30px rgba(0,0,0,.35)}
  .card--front{top:30px;background:var(--paper)}
  .card--back{top:470px;background:linear-gradient(135deg,var(--gold-deep) 0%,#d9b33e 40%,var(--gold-light) 62%,#d4ab35 80%,var(--gold-deep) 100%)}

  /* front */
  .brand{position:absolute;left:44px;top:38px}
  .brand__name{font-weight:300;color:var(--turquoise);font-size:30px;letter-spacing:2px;line-height:1}
  .brand__sub{font-weight:300;color:var(--gold);font-size:13px;letter-spacing:9px;margin-top:4px;padding-left:30px}

  .person{position:absolute;left:44px;top:112px}
  .person__line{font-size:20px;color:var(--turquoise);font-weight:300;white-space:nowrap}
  .person__name{font-family:"Allura",cursive;color:var(--gold);font-size:32px;margin-right:6px}
  .person__roles{font-weight:300;color:var(--ink);font-size:19px;line-height:1.15;margin-top:2px}
  .divider{position:absolute;left:44px;top:218px;width:14px;height:2px;background:var(--gold)}

  .contact{position:absolute;left:44px;top:244px;list-style:none}
  .contact li{display:flex;align-items:center;gap:10px;font-weight:300;color:var(--ink);font-size:19px;line-height:1.4}
  .contact svg{width:15px;height:15px;flex:none}

  .halo{position:absolute;left:420px;top:108px;width:420px;height:420px;border-radius:50%;background:radial-gradient(circle at 40% 40%,#fbf0a6 0%,var(--halo) 55%,#e7cc58 100%)}
  .halo__arc{position:absolute;left:440px;top:126px;width:380px;height:380px;border-radius:50%;border-top:8px solid #fff;border-left:4px solid transparent;border-right:4px solid transparent;transform:rotate(-18deg)}
  .portrait{position:absolute;left:480px;top:178px;width:220px;height:222px;border-top-left-radius:180px 220px;background:linear-gradient(160deg,#e8d190 0%,#d9b98a 40%,#c99c7e 70%,#b5636a 100%)}

  /* back */
  .logo{position:absolute;left:0;right:0;top:120px;display:flex;align-items:center;justify-content:center;gap:16px}
  .logo__mark{width:46px;height:46px;border-radius:50%;border:2px solid var(--turquoise)}
  .logo__name{font-weight:400;color:var(--turquoise);font-size:32px;letter-spacing:3px;line-height:1.1}
  .logo__rule{position:absolute;left:250px;width:200px;height:1px;background:var(--gold-light)}
  .logo__rule--top{top:214px}
  .logo__rule--bottom{top:262px}
  .tagline{position:absolute;left:0;right:0;top:224px;text-align:center;font-weight:300;color:var(--ink-dark);font-size:22px}
</style>
</head>
<body>

<section class="card card--front" aria-label="Business card, contact side">
  <div class="halo"></div>
  <div class="halo__arc"></div>
  <div class="portrait" role="img" aria-label="Portrait photo of Lina Suzette Brolin"></div>

  <div class="brand">
    <div class="brand__name">VELMORA GROVE</div>
    <div class="brand__sub">COACHING</div>
  </div>

  <div class="person">
    <div class="person__line"><span class="person__name">Lina Suzette Brolin</span>| Life Coach</div>
    <div class="person__roles">Thessing Certified Teacher | Yoga Teacher<br>Interior Designer</div>
  </div>
  <div class="divider"></div>

  <ul class="contact">
    <li>
      <svg viewBox="0 0 16 16" aria-hidden="true"><circle cx="8" cy="8" r="8" fill="#2fb5b8"/><path d="M5.2 4.3l1.4-.3.8 2-1 .7a5 5 0 0 0 2.9 2.9l.7-1 2 .8-.3 1.4c-3.6.4-6.9-2.9-6.5-6.5z" fill="#fff"/></svg>
      614-372-0583
    </li>
    <li>
      <svg viewBox="0 0 16 16" aria-hidden="true"><rect x="1" y="3" width="14" height="10" rx="1.5" fill="#2fb5b8"/><path d="M2 4.5l6 4.5 6-4.5" fill="none" stroke="#fff" stroke-width="1.3"/></svg>
      linasb@quorvamail.com
    </li>
    <li>
      <svg viewBox="0 0 16 16" aria-hidden="true"><circle cx="8" cy="8" r="7.5" fill="#2fb5b8"/><g fill="none" stroke="#fff" stroke-width="1"><ellipse cx="8" cy="8" rx="3" ry="7"/><path d="M1 8h14M2 4.5h12M2 11.5h12"/></g></svg>
      www.velmoragrove.com
    </li>
  </ul>
</section>

<section class="card card--back" aria-label="Business card, brand side">
  <div class="logo">
    <span class="logo__mark"></span>
    <span class="logo__name">VELMORA GROVE COACHING</span>
  </div>
  <div class="logo__rule logo__rule--top"></div>
  <p class="tagline">Transformational Retreats</p>
  <div class="logo__rule logo__rule--bottom"></div>
</section>

</body>
</html>
```